New Web Design Project

Number of Pages Required

1 page

Requirements
Must have
• An Overview / Background of the Business & Services(not for profit rescue animal farm)
• The Target Market / Audience you are trying to reach (animal lovers)
• Design Specifics; any preferences or ideas for Style, Colour, Imagery, etc (no preferences)

```html
<!DOCTYPE html>
<html lang="en">
<head>
<meta charset="utf-8">
<title>Cedar Hollow Farms</title>
<link href="https://fonts.googleapis.com/css2?family=Raleway:wght@600;700;800&family=Open+Sans:wght@400;600;700&display=swap" rel="stylesheet">
<style>
:root{
  --green:#1a9a47;
  --green-dark:#137a37;
  --ink:#222;
  --body:#555;
  --muted:#777;
  --white:#fff;
  --line:#bbb;
}
*{box-sizing:border-box;margin:0;padding:0}
html,body{width:1200px;height:3209px;overflow:hidden;background:var(--white)}
body{font-family:"Open Sans",Arial,sans-serif;color:var(--ink);position:relative}
.abs{position:absolute}
.heading{font-family:"Raleway",Arial,sans-serif;font-weight:700}
.btn{position:absolute;display:flex;align-items:center;justify-content:center;border-radius:30px;font-weight:700;font-size:16px;text-transform:uppercase;color:var(--white);text-decoration:none;letter-spacing:.2px}
.btn-solid{background:var(--green)}
.btn-ghost{border:2px solid var(--white)}

/* header */
.site-header{position:absolute;left:0;top:0;width:1200px;height:157px}
.brand{left:112px;top:76px;font-family:"Raleway",Arial,sans-serif;font-weight:700;font-size:28px;color:var(--ink)}
.call{left:648px;top:52px;font-size:17px;font-weight:600;display:flex;align-items:center;gap:8px}
.call strong{color:var(--green);font-size:22px;font-weight:700}
.header-donate{left:934px;top:43px;width:154px;height:49px;font-size:15px}
.nav{left:450px;top:110px;width:650px;display:flex;justify-content:flex-end;gap:26px;font-size:16px;font-weight:600;align-items:center}
.nav a{color:var(--ink);text-decoration:none}
.nav a.active{color:var(--green)}

/* hero */
.hero{position:absolute;left:0;top:157px;width:1200px;height:549px;
  background:linear-gradient(180deg,#2c3a1d 0%,#4d6b2a 35%,#6f9a3a 65%,#3a4a22 100%)}
.hero-title{position:absolute;top:70px;width:100%;text-align:center;font-size:80px;font-weight:800;color:var(--white)}
.hero-sub{position:absolute;top:186px;width:100%;text-align:center;font-size:30px;color:var(--white)}
.dots{position:absolute;top:481px;left:565px;display:flex;gap:5px}
.dots span{width:14px;height:14px;border-radius:50%;border:2px solid var(--white)}
.dots span.on{background:var(--white)}

/* welcome */
.welcome-title{left:112px;top:822px;font-size:40px;line-height:50px;color:var(--ink)}
.welcome-text{left:112px;top:948px;width:462px;font-size:14.5px;line-height:28px;color:var(--body)}
.welcome-btn{left:112px;top:1122px;width:158px;height:56px}
.feature{position:absolute;left:668px;width:460px;height:116px}
.feature .ring{position:absolute;left:0;top:0;width:116px;height:116px;border-radius:50%;border:1.5px solid var(--line);display:flex;align-items:center;justify-content:center}
.feature h3{position:absolute;left:147px;top:2px;font-family:"Raleway",Arial,sans-serif;font-weight:700;font-size:22px}
.feature p{position:absolute;left:147px;top:44px;width:290px;font-size:14.5px;line-height:27px;color:var(--muted)}

/* donate band */
.donate-band{position:absolute;left:0;top:1310px;width:1200px;height:475px;
  background:linear-gradient(180deg,#5b5f5a 0%,#6f7667 40%,#4e6a2e 70%,#263818 100%);color:var(--white);text-align:center}
.band-title{position:absolute;top:86px;width:100%;font-size:37px}
.band-text{position:absolute;top:150px;left:240px;width:720px;font-size:20px;line-height:35px;font-weight:600}
.band-btn{left:506px;top:262px;width:189px;height:58px}
.band-call{position:absolute;top:352px;width:100%;font-size:36px}

/* programs */
.programs-title{top:1885px;width:1200px;text-align:center;font-size:39px;color:var(--ink)}
.card{position:absolute;top:1990px;width:306px}
.card .photo{width:306px;height:235px;border:5px solid var(--white);box-shadow:0 0 8px rgba(0,0,0,.25)}
.card p{text-align:center;margin-top:24px;font-size:21px;font-weight:600}
.programs-btn{left:521px;top:2338px;width:159px;height:55px}

/* volunteer */
.volunteer{position:absolute;left:0;top:2500px;width:1200px;height:374px;
  background:linear-gradient(180deg,#1f9a4a 0%,#2a9e48 55%,#1d7d36 100%);color:var(--white);text-align:center}
.vol-title{position:absolute;top:66px;width:100%;font-size:37px}
.vol-text{position:absolute;top:132px;left:250px;width:700px;font-size:17px;line-height:32px;font-weight:600}
.vol-btn{left:505px;top:237px;width:190px;height:60px}

/* footer */
.social{left:516px;top:2972px;display:flex;gap:8px}
.social span{width:52px;height:52px;border-radius:50%;border:1.5px solid #999;display:block}
.contact{top:3053px;width:1200px;display:flex;justify-content:center;gap:14px;font-size:14.5px;color:var(--body);align-items:center}
.contact .item{display:flex;align-items:center;gap:7px}
.links{top:3093px;width:1200px;text-align:center;font-size:14.5px;color:var(--body);word-spacing:3px}
.copy{top:3135px;width:1200px;text-align:center;font-size:14.5px;color:var(--body)}
</style>
</head>
<body>

<header class="site-header">
  <div class="abs brand">Cedar Hollow Farms</div>
  <div class="abs call">
    <svg width="16" height="16" viewBox="0 0 24 24"><path fill="#1a9a47" d="M6.6 10.8a15.1 15.1 0 0 0 6.6 6.6l2.2-2.2c.3-.3.7-.4 1-.2 1.1.4 2.3.6 3.6.6.6 0 1 .4 1 1V20c0 .6-.4 1-1 1A17 17 0 0 1 3 4c0-.6.4-1 1-1h3.5c.6 0 1 .4 1 1 0 1.3.2 2.5.6 3.6.1.3 0 .7-.2 1z"/></svg>
    Call us <strong>1 800 555 0147</strong>
  </div>
  <a class="btn btn-solid header-donate" href="#">Donate Now!</a>
  <nav class="abs nav">
    <a class="active" href="#">Home</a><a href="#">About Us</a><a href="#">Programs &amp; Services</a><a href="#">Get Involved</a><a href="#">News</a><a href="#">Contact</a>
    <svg width="16" height="16" viewBox="0 0 24 24"><circle cx="10" cy="10" r="7" fill="none" stroke="#222" stroke-width="3"/><path d="M15 15l6 6" stroke="#222" stroke-width="3"/></svg>
  </nav>
</header>

<section class="hero" role="img" aria-label="Goats grazing in a green pasture behind a wooden fence">
  <h1 class="hero-title heading">CEDAR HOLLOW FARMS</h1>
  <p class="hero-sub">We are Non profit animal rescue farm</p>
  <a class="btn btn-ghost" style="left:397px;top:260px;width:191px;height:61px" href="#">Join us now!</a>
  <a class="btn btn-ghost" style="left:611px;top:260px;width:192px;height:61px" href="#">How to visit!</a>
  <div class="dots"><span class="on"></span><span></span><span></span><span></span></div>
</section>

<section class="welcome">
  <h2 class="abs heading welcome-title">WELCOME TO<br>CEDAR HOLLOW FARMS</h2>
  <p class="abs welcome-text">Nam libero tempore, cum soluta nobis est eligendi optio cumque nihil impedit quo minus id quod maxime placeat facere possimus, omnis voluptas assumenda est, omnis dolor repellendus. Temporibus autem quibusdam et aut officiis debitis aut rerum necessitatibus saepe eveniet ut et voluptates repudiandae sint et moles.</p>
  <a class="btn btn-solid welcome-btn" href="#">Read More</a>

  <div class="feature" style="top:814px">
    <div class="ring"><svg width="60" height="60" viewBox="0 0 60 60" role="img" aria-label="Donation icon"><circle cx="24" cy="20" r="10" fill="#1a9a47"/><circle cx="38" cy="26" r="9" fill="#1a9a47"/><rect x="8" y="40" width="44" height="10" rx="5" fill="#1a9a47"/></svg></div>
    <h3>How can i Donate</h3>
    <p>Temporibus autem quibusdam et auoff iciis debitis aut rerum neces</p>
  </div>
  <div class="feature" style="top:952px">
    <div class="ring"><svg width="60" height="60" viewBox="0 0 60 60" role="img" aria-label="Thumbs up icon"><rect x="8" y="26" width="12" height="26" rx="2" fill="#1a9a47"/><path d="M24 26l10-16c4 0 6 3 5 7l-2 7h12c3 0 5 3 4 6l-4 18c-1 2-2 4-5 4H24z" fill="#1a9a47"/></svg></div>
    <h3>Get Involved</h3>
    <p>Temporibus autem quibusdam et auoff iciis debitis aut rerum neces</p>
  </div>
  <div class="feature" style="top:1090px">
    <div class="ring"><svg width="64" height="60" viewBox="0 0 64 60" role="img" aria-label="Group of members icon"><circle cx="32" cy="16" r="9" fill="#1a9a47"/><circle cx="14" cy="22" r="7" fill="#1a9a47"/><circle cx="50" cy="22" r="7" fill="#1a9a47"/><path d="M18 52c0-12 6-20 14-20s14 8 14 20z" fill="#1a9a47"/><path d="M2 50c0-9 5-15 12-15 3 0 5 1 6 2-2 4-3 8-3 13z" fill="#1a9a47"/><path d="M62 50c0-9-5-15-12-15-3 0-5 1-6 2 2 4 3 8 3 13z" fill="#1a9a47"/></svg></div>
    <h3>Become a Member</h3>
    <p>Temporibus autem quibusdam et auoff iciis debitis aut rerum neces</p>
  </div>
</section>

<section class="donate-band" role="img" aria-label="Dairy cows grazing on a grassy field at dusk">
  <h2 class="band-title heading">DONATE TO OUR FARM TODAY</h2>
  <p class="band-text">Nam libero tempore, cum soluta nobis est eligendi optio cumque nihil impedit quo minus id quod maxime placeat facere possimu</p>
  <a class="btn btn-ghost band-btn" href="#">Donate Now!</a>
  <p class="band-call heading">CALL 1 800 555 0147</p>
</section>

<section class="programs">
  <h2 class="abs heading programs-title">PROGRAM AND SERVICES</h2>
  <div class="card" style="left:112px">
    <div class="photo" role="img" aria-label="Pasture with a black wooden fence and grazing horses" style="background:linear-gradient(180deg,#8fb6e0 0%,#b9d27a 45%,#5f8f2a 100%)"></div>
    <p>Farm Animal Shelter</p>
  </div>
  <div class="card" style="left:447px">
    <div class="photo" role="img" aria-label="Children at summer camp with a pony" style="background:linear-gradient(180deg,#6f8a3a 0%,#9b6a3c 50%,#c84a3c 100%)"></div>
    <p>Summer Camp 2019</p>
  </div>
  <div class="card" style="left:782px">
    <div class="photo" role="img" aria-label="A brown and white goat against a blurred background" style="background:linear-gradient(180deg,#4f7fa8 0%,#7a8f7a 50%,#8a6a4a 100%)"></div>
    <p>Adopt a Farm Animal</p>
  </div>
  <a class="btn btn-solid programs-btn" href="#">View More</a>
</section>

<section class="volunteer" role="img" aria-label="Green tinted meadow with a wooden fence at sunrise">
  <h2 class="vol-title heading">VOLUNTEER OPPORTUNITIES</h2>
  <p class="vol-text">Temporibus autem quibusdam et aut officiis debitis aut rerum necessitatibus saepe eveniet ut et voluptates repudiandae sint et molestiaaque earum rerum</p>
  <a class="btn btn-ghost vol-btn" href="#">Get Involved!</a>
</section>

<footer>
  <div class="abs social" aria-label="Social media links"><span></span><span></span><span></span></div>
  <div class="abs contact">
    <span class="item"><svg width="11" height="15" viewBox="0 0 12 16"><path fill="#1a9a47" d="M6 0a6 6 0 0 0-6 6c0 4.5 6 10 6 10s6-5.5 6-10a6 6 0 0 0-6-6zm0 8.5A2.5 2.5 0 1 1 6 3.5a2.5 2.5 0 0 1 0 5z"/></svg>240 Meadowbrook Road Fernley, NV 89408</span>
    <span>|</span>
    <span class="item"><svg width="13" height="13" viewBox="0 0 24 24"><path fill="#1a9a47" d="M6.6 10.8a15.1 15.1 0 0 0 6.6 6.6l2.2-2.2c.3-.3.7-.4 1-.2 1.1.4 2.3.6 3.6.6.6 0 1 .4 1 1V20c0 .6-.4 1-1 1A17 17 0 0 1 3 4c0-.6.4-1 1-1h3.5c.6 0 1 .4 1 1 0 1.3.2 2.5.6 3.6.1.3 0 .7-.2 1z"/></svg>1 800 555 0147</span>
    <span>|</span>
    <span class="item"><svg width="15" height="12" viewBox="0 0 20 14"><rect width="20" height="14" rx="1" fill="#1a9a47"/><path d="M1 1l9 7 9-7" fill="none" stroke="#fff" stroke-width="1.5"/></svg>info@cedarhollowfarms.org</span>
  </div>
  <p class="abs links">Help &nbsp;| &nbsp;FAQ &nbsp;| &nbsp;Support &nbsp;| &nbsp;Sitemap &nbsp;| &nbsp;Terms Of Use &nbsp;| &nbsp;Privacy Statement</p>
  <p class="abs copy">Cedar Hollow Farms. © 2019 All rights reserved.</p>
</footer>

</body>
</html>
```